FinTech company looking to revamp and expand client-facing interface for our financial models

Pellworth Engines currently has a very simple website that allows clients to interact with our financial models. We are looking to completely redesign the current site and add several extra pages to provide extra functionality. We want the design to have a modern, slick feel, that will work on both a desktop or a tablet. It should be straightforward for clients to move between different pages at any time, and clear from the layout how to interact with the more advanced features. We have included screenshots of existing pages in the attached design brief, as well as sketches of the functionality required by the new pages, but can't provide a direct link to the current site.
Target Market(s)
Professional investors that will be paying to access the interface
Industry/Entity Type
Finance
Number of Pages Required
4 page
Colors
Designer to choose colors to be used in the design.
Look and feel
Each slider illustrates characteristics of the customer's brand and the style your logo design should communicate.

```html
<!DOCTYPE html>
<html lang="en">
<head>
<meta charset="utf-8">
<title>QVANTA – Models</title>
<link rel="stylesheet" href="https://fonts.googleapis.com/css2?family=Open+Sans:wght@400;600;700&family=Arimo:wght@400;700&display=swap">
<style>
:root{
  --white:#ffffff;
  --navy:#003366;
  --navy-dim:#1d3650;
  --ink:#111111;
  --rule:#e2e2e2;
  --page-dim:#404040;
  --tab-active-dim:#2b2b2b;
  --tab-dim:#3a3a3a;
  --table-dim:#393939;
  --row-line:#333333;
  --head-dim:#233d3b;
  --text-dim:#222222;
  --head-text-dim:#4f6a68;
  --teal:#006b66;
  --field-border:#cfcfcf;
}
*{box-sizing:border-box;margin:0;padding:0}
html,body{width:1200px;height:706px;overflow:hidden;background:var(--page-dim)}
body{position:relative;font-family:"Open Sans",Arial,sans-serif}

.topbar{position:absolute;left:0;top:0;width:1200px;height:57px;background:var(--white);display:flex}
.topbar .cell{height:57px;display:flex;align-items:center;justify-content:center;border-right:1px solid var(--rule);font-size:13px;font-weight:700;color:var(--ink);gap:8px}
.topbar .brand{width:170px;font-size:17px;border-right:none}
.topbar .period{width:85px}
.topbar .spacer{width:85px}
.topbar .gap{flex:0 0 60px;border-right:none}
.topbar .is-active{background:var(--navy);color:var(--white)}
.topbar .nav-models{width:116px}
.topbar .nav-sens{width:168px}
.topbar .nav-port{width:152px}
.topbar .nav-back{width:142px}
.topbar svg{width:22px;height:22px}

.view-tabs .tab{position:absolute;display:flex;align-items:center;justify-content:center;font-size:12px;font-weight:600;color:var(--text-dim);letter-spacing:.2px}
.tab-pairs{left:330px;top:113px;width:190px;height:33px;background:var(--tab-dim)}
.tab-etf{left:520px;top:94px;width:146px;height:38px;background:var(--tab-active-dim);border-radius:6px 6px 0 0}
.tab-factors{left:690px;top:113px;width:108px;height:33px}
.tab-new1{left:812px;top:118px;width:146px;height:30px;background:var(--tab-dim)}
.tab-new2{left:962px;top:118px;width:142px;height:30px;background:var(--tab-dim)}
.tab-next{left:1130px;top:118px;width:20px;height:30px}
.tab-add{left:1153px;top:113px;width:38px;height:33px;background:var(--navy-dim);border-radius:4px}

.export{position:absolute;left:1084px;top:187px;display:flex;align-items:center;gap:6px;font-size:16px;font-weight:700;color:var(--text-dim)}

.models-table{position:absolute;left:85px;top:222px;width:1096px;border-collapse:collapse;background:var(--table-dim);font-family:Arimo,Arial,sans-serif;table-layout:fixed}
.models-table th{height:66px;background:var(--head-dim);color:var(--head-text-dim);font-family:"Open Sans",Arial,sans-serif;font-size:15px;font-weight:700;text-align:left;padding-left:10px}
.models-table td{height:65px;color:var(--text-dim);font-size:14.5px;padding-left:10px;line-height:1.35;border-bottom:1px solid var(--row-line)}
.models-table tr:last-child td{border-bottom:none}

.filter-drawer{position:absolute;left:0;top:94px;width:378px;height:218px;background:var(--white);border-radius:0 6px 6px 0}
.filter-handle{position:absolute;left:370px;top:113px;width:55px;height:180px;background:var(--white);border-radius:0 6px 6px 0}
.filter-handle .label{position:absolute;left:26px;top:90px;transform:translate(-50%,-50%) rotate(-90deg);font-size:15px;font-weight:600;letter-spacing:1.5px;color:var(--ink)}
.filter-toggle{position:absolute;left:413px;top:191px;width:24px;height:24px;border-radius:50%;background:var(--navy);border:2px solid var(--white);box-shadow:0 0 0 1px var(--navy)}
.filter-card{position:absolute;left:14px;top:14px;width:350px;height:190px;border:1px solid var(--rule);border-radius:4px;overflow:hidden}
.filter-card h2{height:46px;background:var(--teal);color:var(--white);font-size:16px;font-weight:700;text-align:center;line-height:46px}
.filter-row{display:flex;align-items:center;height:50px;padding-left:16px;font-size:15px;color:var(--ink);border-bottom:1px solid var(--rule)}
.filter-row.last{border-bottom:none}
.filter-row .name{width:80px}
.filter-row b{margin-right:12px}
.filter-row .field{width:143px;height:29px;border:1px solid var(--field-border);border-radius:4px;padding:4px 12px;font-size:15px;box-shadow:inset 0 1px 2px rgba(0,0,0,.08)}
.apply{display:flex;align-items:center;gap:8px;padding-left:14px;font-size:15px;font-weight:600;color:var(--ink);margin-top:-4px}
.apply .box{width:18px;height:18px;border:1px solid #bbb;border-radius:3px}
</style>
</head>
<body>

<header class="topbar">
  <div class="cell brand">QVANTA</div>
  <div class="cell period is-active">250D</div>
  <div class="cell period">83D</div>
  <div class="cell period">42D</div>
  <div class="cell spacer"></div>
  <div class="cell gap"></div>
  <div class="cell nav-models is-active">
    <svg viewBox="0 0 24 24" fill="none" stroke="#fff" stroke-width="2"><path d="M3 11 12 3l9 8"/><path d="M5 10v10h5v-6h4v6h5V10"/></svg>MODELS</div>
  <div class="cell nav-sens">
    <svg viewBox="0 0 24 24" fill="none" stroke="#111" stroke-width="1.4"><circle cx="12" cy="12" r="4"/><circle cx="12" cy="12" r="8" stroke-dasharray="2 2"/></svg>SENSITIVITIES</div>
  <div class="cell nav-port">
    <svg viewBox="0 0 24 24" fill="none" stroke="#111" stroke-width="1.8"><circle cx="7" cy="7" r="4"/><circle cx="17" cy="7" r="4"/><circle cx="7" cy="17" r="4"/><circle cx="17" cy="17" r="4"/></svg>PORTFOLIO</div>
  <div class="cell nav-back">
    <svg viewBox="0 0 24 24" fill="none" stroke="#111" stroke-width="1.8"><rect x="3" y="4" width="18" height="16"/><path d="M6 16l4-5 3 3 5-6"/></svg>BACKTEST</div>
  <div class="cell gap" style="flex:1;border-left:1px solid var(--rule)"></div>
</header>

<nav class="view-tabs">
  <div class="tab tab-pairs">PAIRS</div>
  <div class="tab tab-etf">ETF PAIRS</div>
  <div class="tab tab-factors">FACTORS</div>
  <div class="tab tab-new1">NEW TAB TITLE #1</div>
  <div class="tab tab-new2">NEW TAB TITLE #2</div>
  <div class="tab tab-next"><svg width="14" height="18" viewBox="0 0 14 18" fill="none" stroke="#2a2a2a" stroke-width="2.5"><path d="M3 2l8 7-8 7"/></svg></div>
  <div class="tab tab-add"><svg width="22" height="22" viewBox="0 0 22 22" fill="none" stroke="#4a5d70" stroke-width="1.8"><circle cx="11" cy="11" r="9"/><path d="M11 6v10M6 11h10"/></svg></div>
</nav>

<div class="export"><svg width="24" height="22" viewBox="0 0 24 22" fill="none" stroke="#222" stroke-width="2"><path d="M10 4H3v16h16v-6"/><path d="M12 12 21 3M15 3h6v6"/></svg>Export</div>

<table class="models-table">
  <colgroup>
    <col style="width:104px"><col style="width:123px"><col style="width:108px">
    <col style="width:81px"><col style="width:85px"><col style="width:85px"><col style="width:85px">
    <col style="width:85px"><col style="width:85px"><col style="width:85px"><col style="width:85px"><col style="width:85px">
  </colgroup>
  <thead><tr><th></th><th></th><th></th><th>Quality</th><th>Stat 1</th><th>Stat 2</th><th>Stat 3</th><th>Stat 4</th><th>Stat 5</th><th>Stat 6</th><th>Stat 7</th><th>Stat 8</th></tr></thead>
  <tbody>
    <tr><td>Model 1</td><td>Materials</td><td>2019-07-03<br>12:15:00.000</td><td>30.2288</td><td>2.01574</td><td>23.305</td><td>-0.149368</td><td>22.3054</td><td>4.63714</td><td>0.945706</td><td>2.81949</td><td>2.60858</td></tr>
    <tr><td>Model 2</td><td>Industrials</td><td>2019-07-03<br>12:15:00.000</td><td>32.8694</td><td>0.87307</td><td>32.185</td><td>-0.033692</td><td>33.9911</td><td>11.5693</td><td>-0.472968</td><td>-0.830458</td><td>6.80646</td></tr>
    <tr><td>Model 3</td><td>Consumer<br>Discretionary</td><td>2019-07-03<br>12:15:00.000</td><td>1.66002</td><td>-0.569222</td><td>159.814</td><td>0.0252328</td><td>172.616</td><td>10.2875</td><td>-0.750396</td><td>-0.385309</td><td>4.69146</td></tr>
    <tr><td>Model 4</td><td>Information<br>Technology</td><td>2019-07-03<br>12:15:00.000</td><td>45.6856</td><td>0.412148</td><td>202.488</td><td>0.0084923</td><td>205.834</td><td>11.9094</td><td>-0.137913</td><td>0.449595</td><td>3.85106</td></tr>
    <tr><td>Model 5</td><td>Information<br>Technology</td><td>2019-07-03<br>12:15:00.000</td><td>75.7733</td><td>7.06728</td><td>188.605</td><td>0.016913</td><td>161.665</td><td>3.82241</td><td>0.981019</td><td>1.29847</td><td>3.34927</td></tr>
  </tbody>
</table>

<aside class="filter-handle"><span class="label">FILTERS</span></aside>
<aside class="filter-drawer">
  <div class="filter-card">
    <h2>Filters</h2>
    <div class="filter-row"><span class="name">Quality</span><b>Threshold:</b><span class="field">-10</span></div>
    <div class="filter-row last"><span class="name"><b style="margin:0">Abs.</b> Stat</span><b>Threshold:</b><span class="field">-10</span></div>
    <div class="apply"><span class="box"></span>Apply to all tabs</div>
  </div>
</aside>
<div class="filter-toggle"><svg width="20" height="20" viewBox="0 0 20 20" fill="none" stroke="#fff" stroke-width="1.8"><path d="M15 10H5M9 6l-4 4 4 4"/></svg></div>

</body>
</html>
```